Wordpress Powered Website. Outstanding Design Required. Using Morvenic Theme

Designers will not need to create anything other than the home page but there are some design elements on the home page which also need to be factored in: 6 product place holders and 2-3 slides for a slideshow (with images I provide).

Designers will need to familiarise themselves with the Morvenic theme to make sure that their design will work within the theme.

The winning designer will set up all the pages and navigation in place. This includes social media icons, favicon, widgets, etc. In other words, the home page needs to be designed and coded and the other preset theme pages need to be organised in a way that we can start using the website on completion of the job.

Most of the designs I had last time were too colourful. This needs to be subtle not in your face.

Background to the business/website:
Ridgeway Banners is a new Australian venture which will sell large format printed banners and other signage. The market is very competitive so it is important to stand out visually and to have a website which is clean, easy to navigate and easy to order. It will be a combination of online sales and assisted sales but all sales enquiries will come from the website.

As our business is focused on presentation it is vital to have excellent design.
Purchased theme is Morvenic. Only this theme is to be used.

1. A home page using all the preset features of the Morvenic theme - it will just be basically taking my wireframe and inputting it to the live theme.
2. A three slide slideshow, ideally with an edited video. The static image slides can be provided by me during the handover. Placeholder for now.
Similar to this one: http://thecedarhollow.example.au/

Attached is the logo which must be utilised, although it could also sit on a dark background. There is our mascot as well which can be used but does not have to be included.

Target Market(s)

Primarily B2B (business to business)
Main industries will be Construction, Retail, Community, Events & Trade Shows

Industry/Entity Type

Printing

Coding

Coded - Design and coding required

Font styles to use
Sans Serif

Requirements
Must have
• Must have the design files made to web pages within the Wordpress environment.
Nice to have
• Clean design. Stand out from competitors based on design.
Should not have
• Should not look like any competitor

```html
<!DOCTYPE html>
<html lang="en">
<head>
<meta charset="utf-8">
<title>Ridgeway Banners – Home</title>
<link href="https://fonts.googleapis.com/css2?family=Lato:ital,wght@0,400;0,700;0,900;1,400&display=swap" rel="stylesheet">
<style>
:root{
  --red:#c90b0b;
  --red-dark:#a80808;
  --ink:#3a3a3a;
  --muted:#777;
  --light:#f0f0f0;
  --line:#d6d6d6;
  --footer:#353535;
  --footer-text:#bdbdbd;
  --white:#fff;
}
*{margin:0;padding:0;box-sizing:border-box}
html,body{width:1200px;height:3614px;overflow:hidden}
body{font-family:'Lato',sans-serif;color:var(--ink);background:var(--white);position:relative}
.abs{position:absolute}
.section-title{position:absolute;left:0;width:1200px;text-align:center;font-weight:700;font-size:40px;color:#555;letter-spacing:.5px;text-transform:uppercase}
.body-text{font-size:13px;line-height:22px;color:var(--muted)}

/* hero */
.hero{position:absolute;left:0;top:0;width:1200px;height:622px;background:linear-gradient(100deg,#4a3a2c 0%,#8a6a45 22%,#c9a06a 38%,#9aa0a6 60%,#6d7279 82%,#4a4e54 100%)}
.topbar{position:absolute;top:10px;left:115px;right:115px;height:24px;font-size:12px;color:#eee;display:flex;align-items:center}
.topbar .social{display:flex;gap:10px;margin-right:14px}
.topbar .social span{width:9px;height:9px;background:#ddd;border-radius:2px}
.topbar .right{margin-left:auto;display:flex;gap:24px;align-items:center}
.topbar .search{width:26px;height:24px;background:#222;display:flex;align-items:center;justify-content:center}
.logo{position:absolute;left:112px;top:56px;font-weight:900;font-size:26px;color:var(--white);letter-spacing:.5px;line-height:1}
.logo small{display:block;font-size:10px;letter-spacing:3px;font-weight:900;margin-top:3px}
.nav{position:absolute;left:318px;top:60px;display:flex;gap:6px;font-size:14px;font-weight:700;color:var(--white)}
.nav a{padding:6px 8px;text-decoration:none;color:inherit}
.nav a.active{background:var(--red);border-radius:3px}
.cart{position:absolute;left:920px;top:62px;font-size:12px;color:#eee;display:flex;gap:8px;align-items:center}
.quote-btn{position:absolute;left:1028px;top:50px;width:58px;height:50px;background:#f26a10;color:#fff;font-weight:900;font-size:12px;text-align:center;padding-top:10px;line-height:14px;border-radius:0 0 4px 4px}
.billboard{position:absolute;left:520px;top:150px;width:460px;height:310px;background:linear-gradient(160deg,#e8e0d6,#b8a592);border:6px solid #3d3d3d}
.promo{position:absolute;left:200px;top:525px;width:800px;height:150px;background:var(--red);color:#fff;padding:30px 38px}
.promo h2{font-size:30px;font-weight:700;letter-spacing:.5px}
.promo p{font-size:18px;line-height:28px;margin-top:8px}
.promo .btn{position:absolute;right:38px;top:53px;width:188px;height:64px;border:2px solid #fff;border-radius:6px;display:flex;align-items:center;justify-content:center;font-size:18px}

/* about */
.about-title{top:758px}
.about-title .accent{color:var(--red)}
.about-lead{position:absolute;top:830px;left:0;width:1200px;text-align:center;font-style:italic;font-size:17px;color:#555}
.about-text{position:absolute;top:862px;left:170px;width:860px;text-align:center}
.small-btn{position:absolute;width:132px;height:38px;background:var(--red);color:#fff;font-weight:700;font-size:12px;border-radius:4px;display:flex;align-items:center;justify-content:center}

/* services */
.services{position:absolute;top:1062px;left:0;width:1200px;height:462px;background:var(--light)}
.service-card{position:absolute;top:128px;width:294px;height:273px;background:#e6e6e6;padding:28px 26px}
.service-card.active{background:#fff;border:1px solid var(--line)}
.service-card h3{font-size:26px;font-weight:400;color:#333;margin:20px 0 12px}

/* projects */
.filters{position:absolute;top:1648px;left:0;width:1200px;display:flex;justify-content:center;gap:22px}
.filters span{height:40px;padding:0 22px;border:1px solid var(--line);border-radius:3px;font-size:12px;display:flex;align-items:center;color:#555}
.filters span.active{background:var(--red);border-color:var(--red);color:#fff;font-weight:700;padding:0 24px}
.tile{position:absolute;border-radius:8px;overflow:hidden}
.plus{position:absolute;left:50%;top:50%;width:56px;height:56px;margin:-28px 0 0 -28px;border:3px solid #fff;border-radius:50%;background:rgba(255,255,255,.25)}
.plus::before,.plus::after{content:"";position:absolute;background:#fff;left:50%;top:50%}
.plus::before{width:22px;height:3px;margin:-1.5px 0 0 -11px}
.plus::after{width:3px;height:22px;margin:-11px 0 0 -1.5px}
.caption{position:absolute;left:18px;bottom:20px;width:410px;height:112px;background:rgba(201,11,11,.92);color:#fff;padding:16px 18px}
.caption h4{font-size:22px;font-weight:700}
.caption p{font-size:13px;line-height:18px;margin-top:8px}

/* features */
.features-title{top:2286px;font-size:28px;color:#555}
.feature{position:absolute;top:2362px;width:196px;height:248px;border:2px solid var(--line);border-radius:6px;text-align:center;padding-top:28px}
.feature h4{font-size:17px;font-weight:400;color:#333;line-height:24px;margin-top:16px}
.feature p{font-size:12px;line-height:20px;color:var(--muted);margin-top:10px;padding:0 14px}

/* testimonial */
.testimonial{position:absolute;top:2680px;left:0;width:1200px;height:540px;background:linear-gradient(180deg,#6e6e6e,#8a8784 45%,#5c5a58)}
.testimonial .section-title{color:#fff;top:62px}
.quote-mark{position:absolute;top:150px;font-size:230px;line-height:1;color:rgba(255,255,255,.45);font-weight:900;font-family:'Lato',sans-serif}
.avatar{position:absolute;left:542px;top:147px;width:116px;height:116px;border-radius:50%;border:5px solid rgba(255,255,255,.85);background:linear-gradient(160deg,#c7b3a0,#7e6c60)}
.t-name{position:absolute;top:280px;width:1200px;text-align:center;color:#fff;font-size:24px}
.t-text{position:absolute;top:322px;left:205px;width:790px;text-align:center;color:#fff;font-style:italic;font-size:15px;line-height:27px}

/* newsletter & footer */
.footer{position:absolute;top:3205px;left:0;width:1200px;height:409px;background:var(--footer)}
.newsletter{position:absolute;top:3150px;left:200px;width:800px;height:103px;background:var(--red)}
.newsletter .field{position:absolute;left:58px;top:28px;width:564px;height:48px;border:2px solid #fff;border-radius:8px;color:#fff;font-size:14px;padding:14px 20px}
.newsletter .send{position:absolute;left:680px;top:22px;width:62px;height:62px;background:#fff;border-radius:50%}
.footer h5{position:absolute;top:130px;color:#fff;font-size:14px;font-weight:700;letter-spacing:.5px}
.links{position:absolute;top:162px;list-style:none;font-size:13px;color:var(--footer-text);line-height:28.5px}
.links li::before{content:"›";margin-right:8px;color:#999}
.contact{position:absolute;left:420px;top:162px;font-size:13px;color:var(--footer-text);line-height:18px}
.contact .row{display:flex;gap:10px;margin-bottom:12px}
.contact .phone{font-size:18px;color:#fff;font-weight:700}
.map{position:absolute;left:626px;top:170px;width:196px;height:130px;background:linear-gradient(135deg,#e9e9e6,#c9cbc6);border:1px solid #999}
.flogo{position:absolute;left:880px;top:132px;font-weight:900;font-size:30px;color:#8a8a8a;line-height:1}
.flogo small{display:block;font-size:12px;letter-spacing:4px;margin-top:4px}
.copy{position:absolute;left:880px;top:218px;font-size:13px;color:var(--footer-text);line-height:20px}
.copy b{color:#fff}
</style>
</head>
<body>

<!-- Hero -->
<header class="hero">
  <div class="billboard" role="img" aria-label="Bus stop billboard photo advertising a hair salon in a sunlit city street"></div>
  <div class="topbar">
    <div class="social"><span></span><span></span><span></span><span></span></div>
    <span>QUESTION CALL : <b>123 555 0147</b></span>
    <div class="right"><span>LANGUAGES</span><span>SUPPORT</span><span>LOGIN</span>
      <span class="search"><svg width="12" height="12" viewBox="0 0 12 12"><circle cx="5" cy="5" r="3.6" fill="none" stroke="#fff" stroke-width="1.6"/><line x1="7.6" y1="7.6" x2="11" y2="11" stroke="#fff" stroke-width="1.6"/></svg></span>
    </div>
  </div>
  <div class="logo">RIDGEWAY<small>BANNERS</small></div>
  <nav class="nav">
    <a class="active">HOME</a><a>ABOUT US</a><a>SERVICES</a><a>PRODUCTS</a><a>TESTIMONIALS</a><a>CONTACT US</a>
  </nav>
  <div class="cart">
    <svg width="22" height="18" viewBox="0 0 22 18"><path d="M1 2h4l3 10h10l2-7H7" fill="none" stroke="#fff" stroke-width="1.6"/><circle cx="9" cy="15.5" r="1.6" fill="#fff"/><circle cx="17" cy="15.5" r="1.6" fill="#fff"/></svg>
    <span>MY CART</span>
  </div>
  <div class="quote-btn">FREE<br>QUOTE</div>
</header>

<svg class="abs" style="left:220px;top:660px" width="760" height="66" viewBox="0 0 760 66"><path d="M0 0h760v10Q380 110 0 10z" fill="#d8d8d8"/></svg>
<section class="promo">
  <h2>ONE STOP SOLUTION</h2>
  <p>FOR ALL YOUR PRINTING AND SIGNAGE NEEDS<br>WITH &nbsp;MOST AFFORDABLE PRICES</p>
  <div class="btn">KNOW MORE</div>
</section>

<!-- About -->
<h2 class="section-title about-title">About <span class="accent">Ridgeway</span> Banners</h2>
<p class="about-lead">Lorem ipsum dolor sit amet, consectetuer adipiscing elit, sed diam nonummy nibh euismod tincidunt</p>
<p class="about-text body-text">Lorem ipsum dolor sit amet, consectetuer adipiscing elit, sed diam nonummy nibh euismod tincidunt ut laoreet dolore magna aliquam erat volutpat. Ut wisi enim ad minim veniam, quis nostrud exerci tation ullamcorper suscipit lobortis nisl ut aliquip ex ea commodo consequat. Duis autem vel eum iriure dolor in hendrerit in vulputate velit esse molestie consequat, vel illum dolore eu feugiat nulla facilisis at vero eros et accumsan et iusto odio dignissim qui blandit praesent luptatum zzril delenit augue duis dolore te feugait nulla facilisi.</p>
<div class="small-btn" style="left:534px;top:982px">KNOW MORE</div>

<!-- Services -->
<section class="services">
  <h2 class="section-title" style="top:66px">Our Services</h2>
  <div class="service-card active" style="left:111px">
    <svg width="50" height="50" viewBox="0 0 50 50" fill="none" stroke="#f26a10" stroke-width="4"><rect x="6" y="8" width="38" height="20"/><line x1="14" y1="28" x2="10" y2="46"/><line x1="36" y1="28" x2="40" y2="46"/><line x1="8" y1="38" x2="42" y2="38"/><line x1="25" y1="2" x2="25" y2="8"/></svg>
    <h3>Banner Design</h3>
    <p class="body-text">Lorem ipsum dolor sit amet, consec tetuer adipiscing elit, sed diam nonu mmy nibh euismod tincidunt ut laoreet dolor sit amet, consec tetuer</p>
  </div>
  <div class="service-card" style="left:453px">
    <svg width="50" height="50" viewBox="0 0 50 50" fill="none" stroke="#5bbf2a" stroke-width="4"><path d="M12 4h26l-4 28H8z"/><line x1="12" y1="32" x2="6" y2="48"/><line x1="34" y1="32" x2="42" y2="48"/></svg>
    <h3>Poster Design</h3>
    <p class="body-text">Lorem ipsum dolor sit amet, consec tetuer adipiscing elit, sed diam nonu mmy nibh euismod tincidunt ut laoreet dolor sit amet, consec tetuer</p>
  </div>
  <div class="service-card" style="left:795px">
    <svg width="50" height="50" viewBox="0 0 50 50" fill="none" stroke="#2a7fc9" stroke-width="4"><line x1="25" y1="2" x2="25" y2="48"/><path d="M6 6h30l6 6-6 6H6z"/><path d="M44 22H14l-6 6 6 6h30z"/></svg>
    <h3>Signage</h3>
    <p class="body-text">Lorem ipsum dolor sit amet, consec tetuer adipiscing elit, sed diam nonu mmy nibh euismod tincidunt ut laoreet dolor sit amet, consec tetuer</p>
  </div>
</section>

<!-- Projects -->
<h2 class="section-title" style="top:1570px">Some of our latest projects</h2>
<div class="filters"><span class="active">ALL PRODUCTS</span><span>BANNERS</span><span>POSTERS</span><span>SIGNAGE</span><span>FABRICS</span><span>STICKERS</span></div>

<div class="tile" style="left:111px;top:1725px;width:443px;height:444px;background:linear-gradient(160deg,#8a9a78,#5b5f5a 55%,#3d3f40)" role="img" aria-label="Street-side poster display promoting a door entry product">
  <div class="caption"><h4>Halden Doorway Banner</h4><p>Lorem ipsum dolor sit amet, consec tetuer adipiscing elit, sed diam nonu mmy nibh euismod tincidunt ut laoreet dolor sit</p></div>
</div>
<div class="tile" style="left:590px;top:1725px;width:232px;height:203px;background:linear-gradient(150deg,#7d8c6a,#b9aa97)" role="img" aria-label="Illuminated street poster in a park"><span class="plus"></span></div>
<div class="tile" style="left:856px;top:1725px;width:231px;height:203px;background:linear-gradient(150deg,#8d2a2a,#c9c2bb 60%,#6b6b6b)" role="img" aria-label="Row of red promotional panels at a station"><span class="plus"></span></div>
<div class="tile" style="left:590px;top:1966px;width:232px;height:203px;background:linear-gradient(150deg,#9aa4a8,#d2d4d2 55%,#7c8488)" role="img" aria-label="Bus shelter advertising panel"><span class="plus"></span></div>
<div class="tile" style="left:856px;top:1966px;width:231px;height:203px;background:linear-gradient(150deg,#5a6a7c,#a9b2b8 55%,#48505a)" role="img" aria-label="Glass bus shelter with poster display"><span class="plus"></span></div>

<!-- Features -->
<h2 class="section-title features-title">So, among other features, here's a few of them</h2>
<div class="feature" style="left:159px">
  <svg width="64" height="64" viewBox="0 0 64 64"><path d="M32 8C16 8 6 20 6 32s10 22 22 22c4 0 5-3 3-6s0-6 4-6h7c10 0 16-6 16-14C58 16 46 8 32 8z" fill="#6b6b6b"/><circle cx="20" cy="26" r="4" fill="#fff"/><circle cx="32" cy="18" r="4" fill="#fff"/><circle cx="44" cy="24" r="4" fill="#fff"/><line x1="38" y1="50" x2="58" y2="30" stroke="#6b6b6b" stroke-width="5"/></svg>
  <h4>FREE DESIGN<br>SERVICE</h4>
  <p>Lorem ipsum dolor sit amet, consec tetuer adipiscing</p>
</div>
<div class="feature" style="left:388px">
  <svg width="64" height="64" viewBox="0 0 64 64"><circle cx="32" cy="24" r="16" fill="#6b6b6b"/><circle cx="32" cy="24" r="8" fill="none" stroke="#fff" stroke-width="3"/><path d="M22 36l-6 22 8-4 5 7 3-16zM42 36l6 22-8-4-5 7-3-16z" fill="#6b6b6b"/></svg>
  <h4>ENSURE<br>QUALITY</h4>
  <p>Lorem ipsum dolor sit amet, consec tetuer adipiscing</p>
</div>
<div class="feature" style="left:615px">
  <svg width="76" height="64" viewBox="0 0 76 64"><rect x="4" y="16" width="40" height="30" fill="#6b6b6b"/><path d="M46 24h14l10 12v10H46z" fill="#6b6b6b"/><circle cx="16" cy="50" r="6" fill="#6b6b6b" stroke="#fff" stroke-width="2"/><circle cx="58" cy="50" r="6" fill="#6b6b6b" stroke="#fff" stroke-width="2"/></svg>
  <h4>FAST<br>DELIVERY</h4>
  <p>Lorem ipsum dolor sit amet, consec tetuer adipiscing</p>
</div>
<div class="feature" style="left:843px">
  <svg width="70" height="64" viewBox="0 0 70 64" fill="#6b6b6b"><circle cx="22" cy="38" r="16"/><text x="22" y="45" text-anchor="middle" font-size="20" font-weight="900" fill="#fff" font-family="Lato,sans-serif">$</text><rect x="42" y="10" width="24" height="8" rx="3"/><rect x="42" y="21" width="24" height="8" rx="3"/><rect x="42" y="32" width="24" height="8" rx="3"/><rect x="42" y="43" width="24" height="8" rx="3"/></svg>
  <h4>PRICE<br>GUARANTEE</h4>
  <p>Lorem ipsum dolor sit amet, consec tetuer adipiscing</p>
</div>

<!-- Testimonial -->
<section class="testimonial" role="img" aria-label="Blurred office background photo">
  <h2 class="section-title">Here's what our customers say</h2>
  <span class="quote-mark" style="left:130px">“</span>
  <span class="quote-mark" style="left:972px">”</span>
  <div class="avatar" role="img" aria-label="Customer portrait"></div>
  <p class="t-name">Owen Marsh</p>
  <p class="t-text">Lorem ipsum dolor sit amet, consec tetuer adipiscing elit, sed diam nonu mmy nibh euismod tincidunt ut laoreet dolor sit amet, consec tetuer lorem ipsum dolor sit amet, consec tetuer adipiscing elit, sed diam nonu mmy nibh euismod tincidunt ut laoreet dolor sit amet, consec tetuer</p>
</section>

<!-- Footer -->
<footer class="footer">
  <h5 style="left:115px">QUICK LINKS</h5>
  <ul class="links" style="left:115px"><li>Home</li><li>About Us</li><li>Services</li><li>Products</li><li>Testimonials</li><li>Contact Us</li></ul>
  <ul class="links" style="left:250px"><li>Login/Register</li><li>My Account</li><li>My Orders</li><li>Support</li><li>Privacy Policy</li><li>Sitemap</li></ul>
  <h5 style="left:420px">CONTACT DETAILS</h5>
  <div class="contact">
    <div class="row"><svg width="12" height="16" viewBox="0 0 12 16"><path d="M6 0a6 6 0 0 0-6 6c0 4 6 10 6 10s6-6 6-10a6 6 0 0 0-6-6z" fill="#bbb"/><circle cx="6" cy="6" r="2.2" fill="#353535"/></svg><span>RIDGEWAY BANNERS,<br>Lorem ipsum dolor sit amet,<br>consec tetuer adipiscing</span></div>
    <div class="row" style="margin-top:14px"><svg width="14" height="10" viewBox="0 0 14 10"><rect width="14" height="10" fill="#bbb"/><path d="M0 0l7 6 7-6" fill="none" stroke="#353535" stroke-width="1.2"/></svg><span>info@ridgewaybanners.com</span></div>
    <div class="row"><svg width="14" height="16" viewBox="0 0 14 16"><path d="M3 0h3l1 4-2 2c1 2 3 4 5 5l2-2 4 1v3c0 2-2 3-4 2C6 14 1 9 0 4c0-2 1-4 3-4z" fill="#bbb"/></svg><span class="phone">123 555 0147</span></div>
  </div>
  <div class="map" role="img" aria-label="Street map showing the office location"></div>
  <div class="flogo">RIDGEWAY<small>BANNERS</small></div>
  <p class="copy">Copyright 2015 <b>RidgewayBanners</b>.<br>All Rights Reserved.</p>
</footer>

<svg class="abs" style="left:215px;top:3248px" width="770" height="40" viewBox="0 0 770 40"><path d="M0 0h770v4Q385 60 0 4z" fill="#2a2a2a"/></svg>
<section class="newsletter">
  <div class="field">ENTER YOUR EMAIL ADDRESS</div>
  <svg class="abs" style="left:620px;top:50px" width="62" height="26" viewBox="0 0 62 26"><path d="M2 2c20 0 20 20 58 20" fill="none" stroke="#fff" stroke-width="2" stroke-dasharray="4 4"/></svg>
  <div class="send"><svg width="62" height="62" viewBox="0 0 62 62"><path d="M18 32l26-12-8 24-6-8z" fill="var(--red)"/><path d="M30 36l14-16" stroke="#fff" stroke-width="1.5"/></svg></div>
</section>

</body>
</html>
```